Velvet Lantern rebranding my business with a new business card

I have my new logo and now I need a refresher on my business cards. I really want something fun and fresh. I like black background or anything to make the color pop.
Logo
Name: Velvet Lantern
Contact Info as stated below:
Mira Pellow
555-013-4762
Logo
Name: Velvet Lantern
Mira Pellow
555-013-4762
fb.me/VelvetLanternbyMira
Instagram: @VelvetLanternbyMira

Industry/Entity Type

Business

Contact Information for Business Card

double-sided. Logo on one side. Contact info on the other.

Requirements
Must have
• Logo
• Name: Velvet Lantern
• Contact Info as stated below:
• Mira Pellow
• 555-013-4762
• fb.me/VelvetLanternbyMira
• fb.me/VelvetLanternbyMira

```html
<!DOCTYPE html>
<html lang="en">
<head>
<meta charset="utf-8">
<title>Velvet Lantern – Business Card</title>
<link rel="stylesheet" href="https://fonts.googleapis.com/css2?family=Source+Sans+3:wght@400;600;700&display=swap">
<style>
  :root {
    --stage: #000000;
    --card-top: #f7c3c7;
    --card-mid: #e59cc4;
    --card-bottom: #c963c6;
    --back-mid: #eba9c2;
    --back-bottom: #dc78b8;
    --ink: #1d1320;
    --art-light: #f4c6d6;
    --art-mid: #e9a6cf;
    --art-deep: #cf78c6;
  }
  * { margin: 0; padding: 0; box-sizing: border-box; }
  html, body {
    width: 1200px; height: 900px; overflow: hidden;
    background: var(--stage);
  }
  .stage { position: relative; width: 1200px; height: 900px; }

  .card {
    position: absolute; top: 275px; width: 482px; height: 293px;
    overflow: hidden;
    background: linear-gradient(180deg, var(--card-top) 0%, var(--card-mid) 55%, var(--card-bottom) 100%);
    font-family: "Source Sans 3", "Myriad Pro", sans-serif;
    color: var(--ink);
  }
  .card--front { left: 116px; border-radius: 0 46px 0 50px; }
  .card--back {
    left: 620px; width: 480px; border-radius: 46px 0 50px 0;
    background: linear-gradient(180deg, var(--card-top) 0%, var(--back-mid) 55%, var(--back-bottom) 100%);
  }

  .holder-name {
    position: absolute; left: 25px; top: 38px;
    font-size: 19px; font-weight: 700; letter-spacing: 0.1px;
  }
  .contact-list {
    position: absolute; left: 25px; top: 91px; list-style: none;
    font-size: 13.5px; line-height: 19.7px;
  }
  .contact-list li { display: flex; align-items: center; gap: 6px; }
  .contact-list svg { width: 10px; height: 10px; flex: none; fill: var(--ink); }

  .illustration-area {
    position: absolute; top: 92px; bottom: 0;
    background: linear-gradient(180deg, var(--art-light) 0%, var(--art-mid) 55%, var(--art-deep) 100%);
    opacity: 0.9;
  }
  .illustration-area--front { left: 266px; right: 0; border-radius: 160px 0 0 0; }
  .illustration-area--back { left: 0; width: 212px; border-radius: 0 160px 0 0; }

  .brand-mark {
    position: absolute; left: 284px; top: 175px;
    display: flex; align-items: center; gap: 8px;
    font-size: 17px; font-weight: 600; color: var(--ink);
    white-space: nowrap;
  }
  .brand-mark .dot {
    width: 12px; height: 12px; border-radius: 50%; background: var(--ink); flex: none;
  }
</style>
</head>
<body>
<main class="stage">
  <section class="card card--front" aria-label="Card front, contact details">
    <div class="illustration-area illustration-area--front" role="img" aria-label="Left half of a large illustrated cupcake with pink swirled frosting and a cherry"></div>
    <h1 class="holder-name">Mira Pellow</h1>
    <ul class="contact-list">
      <li>
        <svg viewBox="0 0 10 10" aria-hidden="true"><path d="M2 0.5 L3.6 2.6 L2.7 3.6 C3.3 5 4.8 6.5 6.4 7.3 L7.4 6.4 L9.5 8 L8.4 9.5 C4.5 9 1 5.5 0.5 1.6 Z"/></svg>
        <span>555-013-4762</span>
      </li>
      <li>
        <svg viewBox="0 0 10 10" aria-hidden="true"><path d="M0.5 2 H9.5 V8.5 H0.5 Z M1 2.4 L5 5.4 L9 2.4" stroke="#f0b6c8" stroke-width="0.8"/></svg>
        <span>info@youremail.com</span>
      </li>
      <li>
        <svg viewBox="0 0 10 10" aria-hidden="true"><circle cx="5" cy="5" r="4.6"/><path d="M2 3.5 C3.5 3 4 5 5.5 4.5 M4 8 C5 6.5 7 7 8 6" stroke="#f0b6c8" stroke-width="0.8" fill="none"/></svg>
        <span>www.website.com</span>
      </li>
      <li>
        <svg viewBox="0 0 10 10" aria-hidden="true"><rect x="1.5" y="1.5" width="7" height="7"/></svg>
        <span>fb.me/VelvetLanternbyMira</span>
      </li>
    </ul>
  </section>

  <section class="card card--back" aria-label="Card back, brand">
    <div class="illustration-area illustration-area--back" role="img" aria-label="Right half of the illustrated cupcake with frosting, cherry and cake base"></div>
    <div class="brand-mark">
      <span class="dot" aria-hidden="true"></span>
      <span>Velvet Lantern</span>
    </div>
  </section>
</main>
</body>
</html>
```